Business Cards Design for the electrical wholesaler: clean bold dynamic :)

We need a business card design that would follow our latest brand guidelines. As an electrical wholesaler we want to bring a fresh look and feel into the industry. The design should be clean bold and dynamic. It should come alive with the renewed energy of our green colour. Our grey colour should keep things balanced and complement the notion of maturity and responsibility. We employ Lato as a corporate font however are not bound by this font and we’re open to interpretation here.

Target Market(s)

Electrical contractors

Industry/Entity Type

Business

Contact Information for Business Card

Logo
Name & Surname: Halyna Dorosh
Job Title: Director of Marketing
Email: halya.dorosh@quillmail.example
Cell phone: XXX.XXX.XXXX
Address: 20517 - 87 Ave. Edmonton, AB, Canada. T6K 4N8
Business Phone: 780.555.0184
Website: www.brovix.example

Font styles to use
Other font styles liked:
• Lato

Requirements
Must have
• Logo & website
Nice to have
• Brand elements - some of them you may find in the attached Brand Guidelines (e.g. three lines on the background signifying "W")

```html
<!DOCTYPE html>
<html lang="en">
<head>
<meta charset="utf-8">
<title>Business Card – brovix</title>
<link href="https://fonts.googleapis.com/css2?family=Work+Sans:wght@400;500;600&display=swap" rel="stylesheet">
<style>
  :root {
    --green: #8dc63f;
    --grey: #58595b;
    --ink: #333333;
    --paper: #ffffff;
    --backdrop: #1d1d1d;
  }
  * { margin: 0; padding: 0; box-sizing: border-box; }
  html, body { width: 1200px; height: 897px; overflow: hidden; }
  body {
    background: var(--backdrop);
    font-family: "Work Sans", Arial, sans-serif;
    position: relative;
  }
  .card {
    position: absolute;
    left: 303px;
    width: 595px;
    height: 339px;
    border-radius: 20px;
    overflow: hidden;
  }
  .card--front { top: 92px; background: var(--paper); }
  .card--back { top: 469px; background: var(--green); }

  .name-band__tab {
    position: absolute; left: 0; top: 38px; width: 24px; height: 63px;
    background: var(--grey);
  }
  .name-band {
    position: absolute; left: 31px; top: 38px; width: 390px; height: 63px;
    background: var(--green); color: var(--paper);
    padding: 6px 0 0 13px;
  }
  .name-band__name { font-size: 24px; font-weight: 500; line-height: 1.2; letter-spacing: 0.2px; }
  .name-band__title { font-size: 15px; font-weight: 400; letter-spacing: 0.6px; }

  .brand-mark {
    position: absolute; right: 38px; top: 44px;
    font-size: 44px; font-weight: 600; color: var(--green);
    letter-spacing: -0.5px; line-height: 1;
  }

  .contact-list {
    position: absolute; left: 36px; top: 254px; list-style: none;
    font-size: 15px; color: var(--ink); letter-spacing: 0.4px;
  }
  .contact-list li { display: flex; align-items: center; height: 19px; }
  .contact-list svg { width: 10px; height: 10px; margin-right: 9px; flex: none; }
  .contact-list .accent { color: var(--green); }

  .address {
    position: absolute; right: 38px; top: 254px; text-align: right;
    font-size: 15px; color: var(--ink); letter-spacing: 0.5px; line-height: 19px;
  }
  .footer-strip { position: absolute; left: 0; bottom: 0; width: 595px; height: 28px; }

  .back-brand {
    position: absolute; left: 0; right: 0; top: 112px; text-align: center; color: var(--paper);
  }
  .back-brand__name { font-size: 72px; font-weight: 500; line-height: 1; letter-spacing: -1px; }
  .back-brand__tagline { font-size: 12px; font-weight: 600; letter-spacing: 1.6px; margin-top: 6px; }
  .back-web {
    position: absolute; left: 0; right: 0; top: 296px; text-align: center;
    color: var(--paper); font-size: 15px; letter-spacing: 0.8px;
  }
</style>
</head>
<body>
  <section class="card card--front">
    <div class="name-band__tab"></div>
    <div class="name-band">
      <div class="name-band__name">Halyna Dorosh</div>
      <div class="name-band__title">Founder</div>
    </div>
    <div class="brand-mark">brovix</div>

    <ul class="contact-list">
      <li>
        <svg viewBox="0 0 10 10"><path d="M2 0.5 L3.6 0.5 L4.2 3 L3 3.8 Q4 6 6.2 7 L7 5.8 L9.5 6.4 L9.5 8 Q9 9.5 7.5 9.5 Q1 8 0.5 2.5 Q0.5 0.5 2 0.5Z" fill="#8dc63f"/></svg>
        780.555.0184
      </li>
      <li>
        <svg viewBox="0 0 10 10"><rect x="0.7" y="2" width="8.6" height="6" fill="none" stroke="#8dc63f" stroke-width="1"/><path d="M0.7 2 L5 5.5 L9.3 2" fill="none" stroke="#8dc63f" stroke-width="1"/></svg>
        halya.dorosh@quillmail.example
      </li>
      <li>
        <svg viewBox="0 0 10 10"><circle cx="5" cy="5" r="4.3" fill="none" stroke="#8dc63f" stroke-width="0.9"/><ellipse cx="5" cy="5" rx="1.9" ry="4.3" fill="none" stroke="#8dc63f" stroke-width="0.9"/><path d="M0.7 5 H9.3" stroke="#8dc63f" stroke-width="0.9"/></svg>
        <span>www.<span class="accent">brovix</span>.example</span>
      </li>
    </ul>

    <div class="address">
      20517 87ave<br>
      T6K4N8 Edmonton, Alberta
    </div>

    <svg class="footer-strip" viewBox="0 0 595 28" preserveAspectRatio="none">
      <rect x="0" y="14" width="310" height="14" fill="#58595b"/>
      <polygon points="305,28 331,0 595,0 595,28" fill="#8dc63f"/>
    </svg>
  </section>

  <section class="card card--back">
    <div class="back-brand">
      <div class="back-brand__name">brovix</div>
      <div class="back-brand__tagline">ELECTRICAL WHOLESALERS</div>
    </div>
    <div class="back-web">www.brovix.example</div>
  </section>
</body>
</html>
```